Business Card Design For Marketing Agnecy LVP

Need business card design for marketing agency.

Doug Fenwick
President, CEO
1-555-302-4196
doug@boldpromoperksgroup.example
www.BoldPromoPerksGroup.example

Back Side:
Boost Sales Using Rewards, Incentives & Giveaways
Get A Free Sample Package

Target Market(s)

B2B

Industry/Entity Type

Marketing

Contact Information for Business Card

Doug Fenwick
President, CEO
1-555-302-4196

Back Side:
Get A Free Sample Package

Please note that my current url is OLD DESIGN. I am working on new design and want the business card to match color themes at least on new site. Here is the demo link for new site so you can see the colors I use, etc.

http://layoutcratehub.example/kq/doug/lvp_final/index.html

Requirements
Must have
• Please note that my current url is OLD DESIGN. I am working on new design and want the business card to match color themes at least on new site. Here is the demo link for new site so you can see the colors I use, etc.

Nice to have

Should not have

```html
<!DOCTYPE html>
<html lang="en">
<head>
<meta charset="utf-8">
<title>LVP Business Card</title>
<link href="https://fonts.googleapis.com/css2?family=Montserrat:wght@700&family=Roboto:wght@400;500;700&family=Roboto+Condensed:wght@400&family=Exo+2:wght@700&display=swap" rel="stylesheet">
<style>
  :root {
    --backdrop: #b7b7b8;
    --brand-blue: #2b5897;
    --charcoal: #3b3c3e;
    --ink: #2f3033;
    --card-light: #f4f4f4;
    --card-mid: #e2e2e3;
    --banner: #eeeeee;
    --watermark: rgba(60, 60, 64, 0.05);
    --white: #ffffff;
  }
  * { box-sizing: border-box; margin: 0; padding: 0; }
  html, body { width: 1200px; height: 576px; overflow: hidden; }
  body { background: var(--backdrop); position: relative; font-family: "Roboto", sans-serif; }

  .card {
    position: absolute;
    top: 138px;
    width: 482px;
    height: 292px;
    border-radius: 9px;
    overflow: hidden;
  }

  .mark-name {
    font-family: "Montserrat", sans-serif; font-weight: 700;
    line-height: 1; letter-spacing: 2px;
  }

  /* Back side */
  .card--back { left: 82px; background: var(--brand-blue); color: var(--white); }
  .back-mark { position: absolute; left: 0; right: 0; top: 34px; text-align: center; }
  .card--back .mark-name { font-size: 104px; color: var(--white); }

  .offer-banner { position: absolute; left: 64px; top: 194px; width: 356px; height: 56px; }
  .offer-banner svg { position: absolute; inset: 0; }
  .offer-text { position: absolute; inset: 0; text-align: center; padding-top: 8px; }
  .offer-tagline { font-size: 13.5px; line-height: 16px; color: var(--ink); }
  .offer-cta { font-size: 13px; line-height: 16px; font-weight: 700; color: var(--brand-blue); margin-top: 4px; letter-spacing: 0.2px; }
  .back-url { position: absolute; left: 0; right: 0; top: 256px; text-align: center; font-size: 13.5px; color: #e8edf5; }

  /* Front side */
  .card--front { left: 602px; background: linear-gradient(160deg, var(--card-light) 0%, #ececec 55%, var(--card-mid) 100%); }
  .front-watermark {
    position: absolute; right: -70px; bottom: -40px;
    font-size: 250px; color: var(--watermark); letter-spacing: 0;
  }
  .holder { position: absolute; left: 27px; top: 46px; }
  .holder-name { font-size: 20px; font-weight: 500; color: var(--brand-blue); }
  .holder-title { font-family: "Roboto Condensed", sans-serif; font-size: 12px; color: var(--ink); margin-top: 3px; }

  .front-mark { position: absolute; right: 38px; top: 40px; }
  .card--front .front-mark .mark-name { font-size: 92px; color: var(--brand-blue); }

  .contact-list { position: absolute; left: 28px; top: 202px; list-style: none; }
  .contact-item {
    display: flex; align-items: center; gap: 8px; height: 18.5px;
    font-family: "Roboto Condensed", sans-serif; font-size: 12.5px; color: var(--ink);
  }
  .contact-icon { width: 11px; height: 11px; flex: none; }

  .base-band { position: absolute; left: 0; right: 0; bottom: 0; height: 10px; background: var(--charcoal); }
  .cta-tab { position: absolute; right: 0; bottom: 0; width: 240px; height: 36px; }
  .cta-tab svg { position: absolute; inset: 0; }
  .cta-tab-text {
    position: absolute; inset: 0; display: flex; align-items: center; justify-content: center;
    padding-left: 22px; padding-top: 2px;
    font-family: "Exo 2", sans-serif; font-weight: 700; font-size: 13px; color: var(--white); letter-spacing: 0.2px;
  }
</style>
</head>
<body>

<section class="card card--back" aria-label="Business card back">
  <div class="back-mark">
    <span class="mark-name">LVP</span>
  </div>
  <div class="offer-banner">
    <svg viewBox="0 0 356 56" width="356" height="56" aria-hidden="true">
      <polygon points="0,0 356,0 348,42 196,42 178,56 160,42 8,42" fill="var(--banner)"/>
    </svg>
    <div class="offer-text">
      <p class="offer-tagline">Boost Sales Using Rewards, Incentives &amp; Giveaways</p>
      <p class="offer-cta">GET A FREE SAMPLE PACKAGE</p>
    </div>
  </div>
  <p class="back-url">www.BoldPromoPerksGroup.example</p>
</section>

<section class="card card--front" aria-label="Business card front">
  <span class="mark-name front-watermark" aria-hidden="true">LVP</span>

  <div class="holder">
    <h1 class="holder-name">Doug Fenwick</h1>
    <p class="holder-title">President, CEO</p>
  </div>

  <div class="front-mark">
    <span class="mark-name">LVP</span>
  </div>

  <ul class="contact-list">
    <li class="contact-item">
      <svg class="contact-icon" viewBox="0 0 12 12" aria-hidden="true">
        <path d="M1 3.5 Q6 0.5 11 3.5 L10 5 L8 4.4 L8 3.6 Q6 3 4 3.6 L4 4.4 L2 5 Z" fill="var(--charcoal)"/>
        <rect x="2.5" y="5.5" width="7" height="5" rx="1" fill="var(--charcoal)"/>
      </svg>
      1-555-302-4196
    </li>
    <li class="contact-item">
      <svg class="contact-icon" viewBox="0 0 12 12" aria-hidden="true">
        <rect x="0.5" y="2.5" width="11" height="7.5" fill="var(--charcoal)"/>
        <polyline points="0.8,2.8 6,7 11.2,2.8" fill="none" stroke="#eeeeee" stroke-width="1"/>
      </svg>
      doug@boldpromoperksgroup.example
    </li>
    <li class="contact-item">
      <svg class="contact-icon" viewBox="0 0 12 12" aria-hidden="true">
        <circle cx="6" cy="6" r="5" fill="none" stroke="var(--charcoal)" stroke-width="1.2"/>
        <ellipse cx="6" cy="6" rx="2.2" ry="5" fill="none" stroke="var(--charcoal)" stroke-width="1"/>
        <line x1="1" y1="6" x2="11" y2="6" stroke="var(--charcoal)" stroke-width="1"/>
      </svg>
      BoldPromoPerksGroup.example
    </li>
  </ul>

  <div class="base-band"></div>
  <div class="cta-tab">
    <svg viewBox="0 0 240 36" width="240" height="36" preserveAspectRatio="none" aria-hidden="true">
      <path d="M12 0 H240 V36 H0 L8 3 Q9 0 12 0 Z" fill="var(--brand-blue)"/>
    </svg>
    <span class="cta-tab-text">Get A Free Sample Package</span>
  </div>
</section>

</body>
</html>
```